Wordpress Theme for Medical Clinics

** Please view updated Sitemap2.pdf doc to clarify some confusion ***

This is a multiuser WordPress subscription site for medical clinics. Please see attachment for sitemap. Please do not include extra content like social media icons, search bars, or images. If you have questions, please ask for clarification.
The site contains the following pages and sub-pages:

1. Home
2. Our Clinic
2a. Our Clinic > Mission
2b. Our Clinic > Services
2c. Our Clinic > Clinic Policies
2d. Our Clinic > Schedules
3. Our Staff
3a. Our Staff > [Staff member page]
4. Resources
4a. Resources > Patient Health (index)
4b. Resources > Patient Health (index) > [post]
4c. Resources > Links
4d. Resources > Forms
5. Alerts
5a. Alerts > [Alert Page]
6. Contact Us

Includes the Following Pages, Subpages, and Content
1. Home
a. About Us
b. Our Staff
c. Bulletins
d. Accepting New Patients (shown as an alert widget)
e. Links
i. Physician Toolbox
ii. Book an Appointment
f. Clinic Policies
i. Show first 3 policies (e.g. Late Arrivals, Missed Appointments, Fees)
ii. Link to Clinic Policies page
g. Primary widget (displayed on all pages)
i. Hours of operation
ii. Contact Info
1. Tel
2. Fax
3. Email
4. Address
5. Get directions (link to Google Maps)
2. Our Clinic
a. Main Page
i. Clinic Name
ii. Overview
iii. Languages Spoken
iv. Secondary Navigation
1. Mission
2. Services
3. Clinic Policies
4. Schedules (see attachment)
b. Our Clinic > Mission
c. Our Clinic > Services
i. For each service include service TITLE and DESCRIPTION
d. Our Clinic > Clinic Policies
i. For each policy include policy TITLE and DESCRIPTION
ii. Include the following policies in mockup
1. Late arrivals
2. Missed appointments
3. Fees for missed appointments
4. Referrals and follow-ups
5. Services not covered by RDA
6. Information for LTF patients
7. Medical Legal Reports
e. Our Clinic > Schedules
3. Our Staff
a. Main Page
i. Display a list of staff members. Include NAME and DESIGNATION
b. Our Staff > [Staff Name]
i. Include NAME, PICTURE, DESIGNATION, and BIO
4. Resources
a. Resources > Patient Health
i. Main Page
1. Posts (ordered by date)
a. Title
b. Summary
2. Side Navigation
a. Post Categories
ii. Patient Health > [post title]
1. Title
2. Post Category
3. Date
4. Author
5. Summary
6. Body
b. Resources > Links
1. Secondary Navigation - Categories
a. Sample Categories:
i. Local Services
ii. RDA and Drug Coverage
iii. Mental Health Resources
2. Category page
a. Include the following links in the 'Local Services' category
i. Hypertension clinics
ii. Home Care services
iii. Vaccine Clinics
c. Resources > Forms
i. Display a table with form TITLE and CATEGORY
ii. Side Navigation
1. Form Categories
a. Use the following sample Categories
i. Referrals
ii. Insurance
iii. Intake
iv. Discharge
v. Waivers
5. Alerts
a. Main page
i. List of all Alert posts
1. Include post TITLE as a link to the post
ii. Side Navigation
1. Alerts Archive
a. shown as Month + Number of posts
iii. Alerts > [Alert page]
1. Include TITLE, DATE, AUTHOR, BODY
6. Contact Us
a. Map
b. Hours of operation
c. Address
d. Phone number
e. Fax number
e. Fax number
f. Map
g. Email

Design notes:
- fixed width
- responsive (need designs for mobile, tablet, and desktop)
- simple, dark font, white background
- use Font Awesome icons where needed
- user adds own logo

Target Market(s)

Medical Clinics

Industry/Entity Type

Medical

Number of Pages Required

5+ page

Font styles to use
Serif
Sans Serif

Requirements
Must have
• Please keep designs very simple.
• Examples:
• https://www.quolbin.com/install
• http://www.ventrohax.com/company/about-us
• http://brindlequota.org/
• http://www.trosk.com/
Should not have
• Minimal or no use of shadows and gradients

```html
<!DOCTYPE html>
<html lang="en">
<head>
<meta charset="utf-8">
<title>Harlow Clinics</title>
<link href="https://fonts.googleapis.com/css2?family=Asap:wght@400;500;600&family=Roboto:wght@400;500&display=swap" rel="stylesheet">
<style>
:root{
  --blue:#1a9fd4;
  --blue-dark:#1587b8;
  --green:#3cb043;
  --ink:#1e1e1e;
  --text:#555;
  --muted:#9a9a9a;
  --band:#eeeeee;
  --line:#d9d9d9;
  --footer:#1c1c1c;
  --footer-bar:#111;
  --white:#fff;
}
*{box-sizing:border-box;margin:0;padding:0}
html,body{width:668px;height:1200px;overflow:hidden;background:var(--white)}
body{font-family:"Roboto",Arial,sans-serif;color:var(--text);position:relative}
.abs{position:absolute}
.head-font{font-family:"Asap",Arial,sans-serif}

/* header */
.brand-mark{left:62px;top:18px;width:16px;height:22px;background:var(--blue)}
.brand-name{left:84px;top:27px;font:500 16px/1 "Asap",sans-serif;color:var(--ink);letter-spacing:.3px}
.contact-label{left:411px;top:24px;font-size:6.5px;color:var(--ink)}
.contact-phone{left:420px;top:33px;font-size:9.5px;color:var(--blue)}
.btn-top{top:21px;width:54px;height:22px;color:var(--white);font-size:6.5px;display:flex;align-items:center;justify-content:center;gap:3px;border-radius:2px}
.btn-login{left:489px;background:var(--green)}
.btn-signup{left:551px;background:var(--blue)}

/* nav */
.nav-band{left:0;top:59px;width:668px;height:31px;background:var(--band)}
.nav-item{top:71px;font-size:6.5px;color:var(--ink)}
.nav-home{left:62px;top:64px;width:38px;height:20px;background:var(--blue);color:var(--white);font-size:6.5px;display:flex;align-items:center;justify-content:center;border-radius:2px}
.nav-active{color:var(--blue)}
.dropdown{left:123px;top:85px;width:101px;height:117px;background:var(--blue);padding-top:6px}
.dropdown li,.submenu li{list-style:none;height:18.2px;line-height:18.2px;padding-left:12px;color:var(--white);font-size:6px;position:relative}
.dropdown li.is-open{background:var(--blue-dark)}
.dropdown .plus{position:absolute;right:10px;top:5.5px;width:7px;height:7px;border-radius:50%;background:var(--white)}
.dropdown .plus::before,.dropdown .plus::after{content:"";position:absolute;background:var(--blue);left:1.5px;top:3px;width:4px;height:1px}
.dropdown .plus::after{left:3px;top:1.5px;width:1px;height:4px}
.submenu{left:227px;top:159px;width:93px;height:49px;background:var(--blue);padding-top:6px}

/* hero */
.hero{left:62px;top:96px;width:544px;height:244px;border:1px solid var(--line);padding:2px}
.hero-photo{width:100%;height:100%;background:linear-gradient(100deg,#d4dade 0%,#e9edef 35%,#c9d3da 60%,#b9cbd9 100%)}
.hero-strip{left:63px;top:236px;width:20px;height:64px;background:var(--blue)}
.hero-dot{left:70px;width:6px;height:6px;border-radius:50%;background:var(--white)}
.hero-dot.on{background:#2b2b2b}
.hero-caption{left:83px;top:236px;width:305px;height:64px;background:rgba(255,255,255,.85);padding:13px 0 0 14px;font:400 13.5px/22px "Roboto",sans-serif;color:#333}
.hero .hero-caption{}

/* sections */
.band{left:0;width:668px;background:var(--band)}
.section-title{font:500 15px/1 "Asap",sans-serif;color:var(--ink);letter-spacing:.3px}
.center{left:0;width:668px;text-align:center}
.copy{font-size:6px;line-height:14px;color:var(--muted)}
.copy .lead{color:var(--ink)}
.avatar{width:54px;height:54px;border-radius:50%;border:2px solid var(--white);box-shadow:0 0 0 1px var(--line);background:linear-gradient(180deg,#e4ecf1,#c3d3de)}
.staff-name{width:140px;text-align:center;font:500 8px/1 "Asap",sans-serif;color:var(--blue);letter-spacing:.3px}
.staff-role{width:140px;text-align:center;font-size:8.5px;color:var(--text)}
.btn-main{height:29px;background:var(--blue);color:var(--white);font:500 8.5px/29px "Asap",sans-serif;text-align:center;border-radius:2px;letter-spacing:.3px}
.patients-copy{left:62px;top:722px;width:354px;font-size:6px;line-height:14.5px;color:var(--text)}
.patients-copy .lead{color:var(--ink)}
.patients-photo{left:434px;top:711px;width:172px;height:116px;border:1px solid var(--line);padding:2px}
.patients-photo div{width:100%;height:100%;background:linear-gradient(120deg,#d8dfe3,#b8c6d2 60%,#5d79a3)}
.field{background:var(--white);border:1px solid var(--line);font-size:6px;color:var(--muted);padding:0 9px;line-height:28px;height:28px}
.field-message{line-height:1;padding-top:10px;height:57px}

/* footer */
.footer{left:0;top:1038px;width:668px;height:120px;background:var(--footer)}
.footer-title{top:1057px;font:500 8px/1 "Asap",sans-serif;color:var(--white);letter-spacing:.3px}
.footer-link{font-size:5.5px;color:#bdbdbd}
.footer-info{font-size:6px;color:#cfcfcf;line-height:9.5px}
.footer-info strong{color:var(--blue);font-weight:500}
.hours-row{left:434px;width:172px;height:23px;border-bottom:1px solid #333;font-size:5.5px;color:#cfcfcf;display:flex;align-items:center}
.hours-row span:first-child{width:73px}
.hours-row:last-child{border-bottom:0}
.footer-bar{left:0;top:1158px;width:668px;height:42px;background:var(--footer-bar)}
.bar-text{top:1175px;font-size:5.5px;color:#8a8a8a}
</style>
</head>
<body>

<!-- header -->
<div class="abs brand-mark"></div>
<div class="abs brand-name">HARLOW CLINICS</div>
<div class="abs contact-label">CONTACT US TODAY!</div>
<div class="abs contact-phone">555-210-4836</div>
<div class="abs btn-top btn-login">
  <svg width="6" height="6" viewBox="0 0 10 10"><circle cx="5" cy="3" r="2.5" fill="#fff"/><path d="M0 10c0-3 2-4.5 5-4.5S10 7 10 10z" fill="#fff"/></svg>LOGIN</div>
<div class="abs btn-top btn-signup">
  <svg width="8" height="6" viewBox="0 0 14 10"><circle cx="5" cy="3" r="2.5" fill="#fff"/><circle cx="10" cy="3" r="2" fill="#fff"/><path d="M0 10c0-3 2-4.5 5-4.5S10 7 10 10zM10.5 10c0-2-.5-3.5-1.5-4.3 3 0 5 1.3 5 4.3z" fill="#fff"/></svg>SIGNUP</div>

<!-- navigation -->
<div class="abs nav-band"></div>
<div class="abs nav-home">HOME</div>
<div class="abs nav-item nav-active" style="left:123px">CLINIC</div>
<div class="abs nav-item" style="left:177px">OUR STAFF</div>
<div class="abs nav-item" style="left:245px">RESOURCES</div>
<div class="abs nav-item" style="left:316px">CONTACT US</div>

<!-- hero -->
<div class="abs hero"><div class="hero-photo" role="img" aria-label="Smiling doctor in a white coat with a colleague in a bright clinic"></div></div>
<div class="abs hero-strip"></div>
<div class="abs hero-dot" style="top:249px"></div>
<div class="abs hero-dot" style="top:260px"></div>
<div class="abs hero-dot on" style="top:271px"></div>
<div class="abs hero-dot" style="top:281px"></div>
<div class="abs hero-caption">LOREM IPSUM DOLOR SIT AMET, CONSEC<br>TETUER ADIPISCING ELIT</div>

<ul class="abs dropdown">
  <li>NAME</li><li>OVERVIEW</li><li>MISSION</li><li>LANGUAGES SPOKEN</li>
  <li class="is-open">SERVICES<span class="plus"></span></li>
  <li>CLINIC POLICIES<span class="plus"></span></li>
</ul>
<ul class="abs submenu"><li>TITLE</li><li>DESCRIPTION</li></ul>

<!-- welcome -->
<div class="abs center section-title" style="top:363px">WELCOME TO HARLOW CLINICS</div>
<div class="abs center copy" style="top:383px;padding:0 62px">
  <span class="lead">Lorem ipsum dolor sit amet, consectetuer adipiscing elit, sed diam nonummy nibh euismod tincidunt ut laoreet dolore magna aliquam erat volutpat.</span><br>
  Ut wisi enim ad minim veniam, quis nostrud exerci tation ullamcorper suscipit lobortis nisl ut aliquip ex ea commodo consequat. Duis autem vel eum iriure dolor in hendrerit in vulp utate velit esse molestie consequat, vel illum dolore eu feugiat nulla facilisis at vero eros et accumsan et iusto odio dignissim.
</div>

<!-- staff -->
<div class="abs band" style="top:440px;height:232px"></div>
<div class="abs center section-title" style="top:459px">OUR STAFFS</div>
<div class="abs center copy" style="top:479px">Lorem ipsum dolor sit amet, consectetuer adipiscing elit, sed diam nonummy nibh euismod tincidunt ut laoreet dolore magna aliquam erat volutpat.</div>

<div class="abs avatar" style="left:103px;top:507px" role="img" aria-label="Portrait of Owen Marsh"></div>
<div class="abs avatar" style="left:238px;top:507px" role="img" aria-label="Portrait of Nora Vale"></div>
<div class="abs avatar" style="left:376px;top:507px" role="img" aria-label="Portrait of Felix Rowe"></div>
<div class="abs avatar" style="left:516px;top:507px" role="img" aria-label="Portrait of Ada Quinn"></div>

<div class="abs staff-name" style="left:60px;top:570px">OWEN MARSH</div>
<div class="abs staff-name" style="left:195px;top:570px">NORA VALE</div>
<div class="abs staff-name" style="left:333px;top:570px">FELIX ROWE</div>
<div class="abs staff-name" style="left:473px;top:570px">ADA QUINN</div>
<div class="abs staff-role" style="left:60px;top:585px">Gynecologist</div>
<div class="abs staff-role" style="left:195px;top:585px">Cardiologist</div>
<div class="abs staff-role" style="left:333px;top:585px">Suspendisse males</div>
<div class="abs staff-role" style="left:473px;top:585px">Gynecologist</div>
<div class="abs btn-main" style="left:287px;top:613px;width:95px">VIEW ALL STAFF</div>

<!-- new patients -->
<div class="abs section-title" style="left:62px;top:699px">NEW PATIENTS</div>
<div class="abs patients-copy">
  <span class="lead">Lorem ipsum dolor sit amet, consectetuer adipiscing elit, sed diam nonummy nibh euismod tincidunt ut laoreet dolore magna aliquam erat volutpat.</span><br>
  Ut wisi enim ad minim veniam, quis nostrud exerci tation ullamcorper suscipit lobortis nisl ut aliquip ex ea commodo consequat. Duis autem vel eum iriure dolor in hendrerit in vulp utate velit esse molestie consequat, vel illum dolore eu feugiat nulla facilisis at vero eros et accumsan et iusto odio dignissim.
</div>
<div class="abs patients-photo"><div role="img" aria-label="Doctor talking with an elderly patient"></div></div>
<div class="abs btn-main" style="left:62px;top:803px;width:95px">CONTACT NOW</div>

<!-- contact -->
<div class="abs band" style="top:867px;height:171px"></div>
<div class="abs section-title" style="left:62px;top:889px">CONTACT US</div>
<div class="abs field" style="left:62px;top:920px;width:172px">Name</div>
<div class="abs field" style="left:248px;top:920px;width:172px">Phone</div>
<div class="abs field" style="left:434px;top:920px;width:172px">Email Address</div>
<div class="abs field field-message" style="left:62px;top:959px;width:451px">Message</div>
<div class="abs btn-main" style="left:526px;top:986px;width:80px;height:30px;line-height:30px">SUBMIT</div>

<!-- footer -->
<div class="abs footer"></div>
<div class="abs footer-title" style="left:62px">QUICK LINKS</div>
<div class="abs footer-title" style="left:250px">CONTACT INFO</div>
<div class="abs footer-title" style="left:434px">HOURS OF OPERATION</div>

<div class="abs footer-link" style="left:63px;top:1074px;line-height:14.4px">Home<br>About Us<br>Our Service<br>FAQ<br>Contact Us</div>
<div class="abs footer-link" style="left:124px;top:1074px;line-height:14.4px">Our Staffs<br>Resources<br>Login<br>Signup</div>

<svg class="abs" style="left:251px;top:1077px" width="6" height="8" viewBox="0 0 6 8"><path d="M3 0a3 3 0 0 1 3 3c0 2-3 5-3 5S0 5 0 3a3 3 0 0 1 3-3z" fill="#1a9fd4"/><circle cx="3" cy="3" r="1" fill="#1c1c1c"/></svg>
<div class="abs footer-info" style="left:262px;top:1076px"><strong>HARLOW CLINICS</strong><br>121 Lorem Ipsm, Lorem Ipsm<br>Lorem Ipsm 10701</div>
<svg class="abs" style="left:250px;top:1113px" width="8" height="6" viewBox="0 0 8 6"><rect width="8" height="6" rx="1" fill="#1a9fd4"/><path d="M0 .5 4 3.5 8 .5" stroke="#1c1c1c" stroke-width=".8" fill="none"/></svg>
<div class="abs footer-info" style="left:263px;top:1111px">info@harlowclinics.example</div>
<svg class="abs" style="left:250px;top:1131px" width="8" height="8" viewBox="0 0 8 8"><rect width="8" height="8" rx="1" fill="#1a9fd4"/><path d="M2.2 1.8c.4 1.9 1.6 3.3 3.8 4.2l.5-1-1.2-.6-.5.5c-.8-.4-1.3-1-1.6-1.7l.5-.5-.5-1.2z" fill="#1c1c1c"/></svg>
<div class="abs footer-info" style="left:265px;top:1130px">555 210 4836</div>

<div class="abs hours-row" style="top:1070px"><span>Monday</span><span>9:00 am - 18:00 pm</span></div>
<div class="abs hours-row" style="top:1093px"><span>Saturday</span><span>9:00 am - 16:00 pm</span></div>
<div class="abs hours-row" style="top:1116px"><span>Sunday</span><span>9:00 am - 14:00 pm</span></div>

<div class="abs footer-bar"></div>
<div class="abs bar-text" style="left:62px">Privacy Policy &nbsp;|&nbsp; Resources &nbsp;|&nbsp; Site Map</div>
<div class="abs bar-text" style="right:62px">© 2011 Harlow Clinics. All rights reserved internationally.</div>

</body>
</html>
```